Business Card for Professional Photographer

I'm looking for an eye catching modern clean design that compliments my logo/ website fonts & colours.
I specialise in architecture, corporate & commercial photography so I'm marketing to professional clients rather than portrait / wedding clients.

I would prefer to not have a solid black design.

My logo brand guide is as follows :

Main front font. : Reislust
Main font colour : #fff
Slogan front font : Ubuntu Bold
Monogram front font : Venti Medium
Container colour : #fff

I need print ready files in pdf .png & .eps formats.

Included in the files below are some screen grabs as reference to font & colours etc.

```html
<!DOCTYPE html>
<html lang="en">
<head>
<meta charset="utf-8">
<title>Northlight Studio – Business Card</title>
<link rel="stylesheet" href="https://fonts.googleapis.com/css2?family=Open+Sans:wght@400;600;700&display=swap">
<style>
  :root {
    --backdrop: #e8e5e1;
    --card: #2a2a2c;
    --gold: #d3ad5b;
    --white: #f4f2ee;
    --shadow: rgba(0, 0, 0, 0.22);
  }
  * { box-sizing: border-box; margin: 0; padding: 0; }
  html, body {
    width: 1200px;
    height: 847px;
    overflow: hidden;
    background: var(--backdrop);
    font-family: "Open Sans", Arial, sans-serif;
  }
  .canvas {
    position: relative;
    width: 1200px;
    height: 847px;
  }
  .card {
    position: absolute;
    top: 270px;
    width: 530px;
    height: 303px;
    background: var(--card);
    box-shadow: 0 14px 30px var(--shadow);
  }
  .card--front { left: 50px; }
  .card--back { left: 620px; }

  /* Front */
  .front-mark {
    position: absolute;
    inset: 0;
    display: flex;
    align-items: center;
    justify-content: center;
  }
  .front-mark__name {
    color: var(--gold);
    font-weight: 400;
    font-size: 22px;
    letter-spacing: 6px;
    text-transform: uppercase;
  }

  /* Back */
  .brand {
    position: absolute;
    top: 42px;
    left: 210px;
  }
  .brand__name {
    color: var(--white);
    font-weight: 400;
    font-size: 19px;
    letter-spacing: 5px;
    text-transform: uppercase;
  }
  .brand__slogan {
    margin-top: 3px;
    color: var(--gold);
    font-weight: 600;
    font-size: 7.5px;
    letter-spacing: 1.6px;
  }
  .divider {
    position: absolute;
    top: 126px;
    left: 34px;
    right: 30px;
    height: 1.5px;
    background: var(--gold);
  }
  .person {
    position: absolute;
    top: 140px;
    left: 240px;
    text-align: center;
  }
  .person__name {
    color: var(--gold);
    font-weight: 700;
    font-size: 22px;
    letter-spacing: 0.3px;
    text-transform: uppercase;
  }
  .person__role {
    color: var(--white);
    font-size: 13px;
    margin-top: -2px;
  }
  .contacts {
    position: absolute;
    top: 140px;
    left: 34px;
    list-style: none;
  }
  .contacts__item {
    display: flex;
    align-items: center;
    gap: 5px;
    color: var(--white);
    font-size: 13px;
    line-height: 21px;
  }
  .contacts__icon {
    width: 10px;
    height: 10px;
    fill: var(--gold);
    flex: none;
  }
  .address {
    position: absolute;
    right: 30px;
    bottom: 26px;
    color: var(--white);
    font-size: 15px;
    line-height: 21px;
    text-align: right;
  }
</style>
</head>
<body>
<main class="canvas">

  <section class="card card--front" aria-label="Card front">
    <div class="front-mark">
      <span class="front-mark__name">Northlight Studio</span>
    </div>
  </section>

  <section class="card card--back" aria-label="Card back">
    <header class="brand">
      <div class="brand__name">Northlight Studio</div>
      <div class="brand__slogan">Architecture Corporate Commercial</div>
    </header>

    <div class="divider"></div>

    <ul class="contacts">
      <li class="contacts__item">
        <svg class="contacts__icon" viewBox="0 0 10 10" aria-hidden="true">
          <path d="M2 0.5 L3.6 2.6 L2.7 3.7 C3.3 5 4.9 6.7 6.3 7.3 L7.4 6.4 L9.5 8 L8.3 9.5 C4.5 9.2 0.8 5.5 0.5 1.7 Z"/>
        </svg>
        555 018 2047
      </li>
      <li class="contacts__item">
        <svg class="contacts__icon" viewBox="0 0 10 10" aria-hidden="true">
          <path d="M0.5 2 H9.5 V8.5 H0.5 Z M0.5 2 L5 5.6 L9.5 2" stroke="#2a2a2c" stroke-width="0.8"/>
        </svg>
        hello@northlightstudio.com
      </li>
      <li class="contacts__item">
        <svg class="contacts__icon" viewBox="0 0 10 10" aria-hidden="true">
          <circle cx="5" cy="5" r="4.6"/>
          <path d="M0.6 5 H9.4 M5 0.5 C3 3 3 7 5 9.5 M5 0.5 C7 3 7 7 5 9.5" stroke="#2a2a2c" stroke-width="0.7" fill="none"/>
        </svg>
        www.northlightstudio.com
      </li>
    </ul>

    <div class="person">
      <div class="person__name">Daniel Ashford</div>
      <div class="person__role">Director</div>
    </div>

    <address class="address" style="font-style: normal;">
      418, Harbor Street<br>
      Riverton NY 10482
    </address>
  </section>

</main>
</body>
</html>
```